Business Card Design Project : Ridgeline Press

In preparation for market launch, Tamarind's Ridgeline Press require the development of a business card. Ridgeline Press is a Community online publishing web portal. We provide the the city of Whistler located in B.C. (Canada) business directories, News, Classified ads, News, Events and blogs etc.

The main focus of the brand is to help local businesses to corporate with their online advertisement and marketing. Meeting our clients face to face is a must (B2B).

Target Market(s)

The target market is B2B customers. Business Owners to Marketing, advertising Managers

Industry/Entity Type

Business

Requirements
Must have
• - The business card will be two sided.
the BACK side will have our logo which consist of (icon, url,slogan) submited. The logo will be middle and centred.

The FRONT side should have company details:

Company Legal Name: TAMARIND RIDGELINE MEDIA

Owen Farsk
Director of Sales & Marketing

www.tamarindridgeline.biz
owen@tamarindridgeline.biz

Phone: 604 317 8842
#2714 - 582 E. Halvern St.
Vancouver, B.C. V7K2R4 Canada
Nice to have
• - For the "FRONT" side of our business card. You can separate or re-arrange with our logo components (icon, logo,slogan). It does not have to be together.

Also our company legal name is rather long so arrange or organize the name in a way to make it shorter. Your experience and creativity will have to come in play.
Should not have
• should not have other colors beside logo color and black text (2 colors). Also nothing Three dimensional

```html
<!DOCTYPE html>
<html lang="en">
<head>
<meta charset="utf-8">
<title>Ridgeline Press — Business Card</title>
<link rel="stylesheet" href="https://fonts.googleapis.com/css2?family=Open+Sans:wght@400;600;700&display=swap">
<style>
  :root {
    --brand-blue: #1f6fb5;
    --ink: #1b1b1b;
    --card: #ffffff;
    --backdrop: #d9dadb;
    --card-edge: #c4c6c8;
  }
  * { margin: 0; padding: 0; box-sizing: border-box; }
  html, body { width: 1200px; height: 944px; overflow: hidden; }
  body {
    background: var(--backdrop);
    font-family: "Open Sans", Arial, sans-serif;
    color: var(--ink);
    position: relative;
  }
  .card {
    position: absolute;
    width: 600px;
    height: 343px;
    background: var(--card);
    border: 1px solid var(--card-edge);
    border-radius: 18px;
    overflow: hidden;
  }

  /* Back side: centred logo lockup */
  .card--back {
    left: 60px;
    top: 60px;
    display: flex;
    flex-direction: column;
    align-items: center;
    justify-content: center;
    text-align: center;
  }
  .back__name {
    display: flex;
    align-items: center;
    gap: 14px;
    font-size: 48px;
    font-weight: 700;
    color: var(--brand-blue);
    line-height: 1;
    margin-bottom: 26px;
  }
  .back__name .dot {
    width: 22px; height: 22px;
    border-radius: 50%;
    background: var(--brand-blue);
  }
  .back__url {
    font-size: 37px;
    font-weight: 700;
    color: var(--ink);
    line-height: 1.05;
    letter-spacing: -0.5px;
  }
  .back__slogan {
    font-size: 29px;
    font-weight: 400;
    color: var(--brand-blue);
    line-height: 1.2;
  }

  /* Front side: contact details */
  .card--front { left: 540px; top: 540px; }
  .front__brand {
    position: absolute;
    left: 40px; top: 48px;
    display: flex;
    align-items: center;
    gap: 10px;
    font-size: 30px;
    font-weight: 700;
    color: var(--brand-blue);
  }
  .front__brand .dot {
    width: 14px; height: 14px;
    border-radius: 50%;
    background: var(--brand-blue);
  }
  .front__slogan {
    position: absolute;
    left: 40px; top: 104px;
    font-size: 16px;
    color: var(--ink);
  }
  .person {
    position: absolute;
    right: 34px; top: 92px;
    text-align: right;
  }
  .person__name { font-size: 23px; font-weight: 600; color: var(--ink); }
  .person__title { font-size: 14px; color: var(--brand-blue); }
  .address {
    position: absolute;
    left: 36px; top: 184px;
    font-size: 15px;
    line-height: 1.4;
    display: flex;
    gap: 8px;
  }
  .contact {
    position: absolute;
    left: 346px; top: 206px;
    font-size: 15px;
    line-height: 1.5;
  }
  .contact__row { display: flex; align-items: center; gap: 8px; }
  .icon { width: 15px; height: 15px; flex: none; fill: var(--brand-blue); }
  .address .icon { margin-top: 3px; }
  .footer-bands { position: absolute; left: 0; bottom: 0; width: 600px; height: 60px; }
  .footer__url {
    position: absolute;
    right: 24px; bottom: 12px;
    font-size: 16px;
    font-weight: 700;
    color: #ffffff;
  }
</style>
</head>
<body>

  <section class="card card--back" aria-label="Business card back">
    <div class="back__name"><span class="dot"></span>Ridgeline Press</div>
    <div class="back__url">www.tamarindridgeline.biz</div>
    <div class="back__slogan">Your information gateway</div>
  </section>

  <section class="card card--front" aria-label="Business card front">
    <div class="front__brand"><span class="dot"></span>Ridgeline Press</div>
    <div class="front__slogan">Your information gateway</div>

    <div class="person">
      <div class="person__name">Owen Farsk</div>
      <div class="person__title">Director of Sales &amp; Marketing</div>
    </div>

    <div class="address">
      <svg class="icon" viewBox="0 0 16 16" aria-hidden="true"><path d="M8 1 L15 8 H13 V15 H9.5 V10.5 H6.5 V15 H3 V8 H1 Z"/></svg>
      <div>#2714 - 582 E. Halvern St.<br>Vancouver, B.C.V7K2R4 Canada</div>
    </div>

    <div class="contact">
      <div class="contact__row">
        <svg class="icon" viewBox="0 0 16 16" aria-hidden="true"><path d="M4 1 C2 2 1.5 4 2.5 6.5 C4 10 6 12 9.5 13.5 C12 14.5 14 14 15 12 L12.5 9.5 L10.5 11 C8.5 10 6 7.5 5 5.5 L6.5 3.5 Z"/></svg>
        <span>604 317 8842</span>
      </div>
      <div class="contact__row">
        <svg class="icon" viewBox="0 0 16 16" aria-hidden="true"><path d="M1 4 H15 V13 H1 Z M1.8 4.6 L8 9 L14.2 4.6" stroke="#fff" stroke-width="1.2"/></svg>
        <span>owen@tamarindridgeline.biz</span>
      </div>
    </div>

    <svg class="footer-bands" viewBox="0 0 600 60" aria-hidden="true">
      <polygon points="0,14 380,14 370,34 0,34" fill="var(--brand-blue)"/>
      <polygon points="345,22 600,22 600,60 330,60" fill="var(--ink)"/>
    </svg>
    <div class="footer__url">www.tamarindridgeline.biz</div>
  </section>

</body>
</html>
```